Update the A4 Specials Page for Restaurant/Cafe

Provide a MINIMALIST attractive Specials page we can print weekly for our food and drink specials to give to our guests. Final design is to be provided in WORD Document so it can be easily edited by Manager. Should be black text and MINIMALIST to minimise ink usage as we print hundreds a week. We have UPLOADED the existing page as a template for you to update. Maybe logo can stay, see what you think. Or delete it and do something else. Keep it simple. Choose a good FONT. Could be a little playful with a cocktail ICON or something. Our existing menus can be seen at www.saltmeadowcafe.com.au and they are using font Alegreya. Please note we are unable to provide any feedback to designers, however we really do appreciate your time if you are submitting a design. Thank you for your participation.

```html
<!DOCTYPE html>
<html lang="en">
<head>
<meta charset="utf-8">
<title>Salt Meadow Cafe – Weekly Specials</title>
<link rel="stylesheet" href="https://fonts.googleapis.com/css2?family=Poppins:wght@400;500;600&display=swap">
<style>
  :root {
    --backdrop: #e6e7e9;
    --paper: #ffffff;
    --ink: #111111;
    --ink-soft: #555555;
    --frame: #222222;
    --accent: #8c1a26;
    --paper-shadow: rgba(0, 0, 0, 0.28);
  }
  html, body {
    margin: 0;
    padding: 0;
    width: 676px;
    height: 1200px;
    overflow: hidden;
    background: var(--backdrop);
  }
  .specials-sheet {
    position: absolute;
    left: 38px;
    top: 175px;
    width: 600px;
    height: 850px;
    background: var(--paper);
    box-shadow: 4px 5px 6px var(--paper-shadow);
  }
  .specials-sheet svg { display: block; width: 100%; height: 100%; }
  .sheet-text { font-family: "Poppins", sans-serif; fill: var(--ink); text-anchor: middle; }
  .section-title { font-size: 19px; font-weight: 600; letter-spacing: 3px; }
  .item-name { font-size: 17px; font-weight: 400; letter-spacing: 2px; }
  .item-name--drink { fill: var(--ink-soft); }
  .item-detail { font-size: 11.5px; font-weight: 400; }
  .item-price { font-size: 17px; font-weight: 600; }
  .brand-tab-text { font-family: "Poppins", sans-serif; font-size: 12.5px; font-weight: 600; fill: var(--paper); letter-spacing: 0.5px; }
  .inner-frame { fill: none; stroke: var(--frame); stroke-width: 1; }
  .brand-tab { fill: var(--accent); }
  .vine-ornament { fill: var(--ink); opacity: 0.85; }
</style>
</head>
<body>
<main class="specials-sheet">
  <svg viewBox="0 0 594 842" xmlns="http://www.w3.org/2000/svg">
    <rect class="inner-frame" x="22.5" y="23.5" width="550" height="796"/>

    <g class="brand">
      <rect class="brand-tab" x="47" y="0" width="44" height="170"/>
      <text class="brand-tab-text" transform="translate(74 152) rotate(-90)">SALT MEADOW CAFE</text>
    </g>

    <g class="food-specials">
      <text class="sheet-text section-title" x="297" y="138">WEEKLY SPECIALS</text>
      <text class="sheet-text item-name" x="297" y="177">CHICKEN FILO</text>
      <text class="sheet-text item-detail" x="297" y="199">Creamy Chicken with Pinenuts. wrapped in Filo Pastry.</text>
      <text class="sheet-text item-detail" x="297" y="218">Served with Side Salad &amp; Zulu Sauce</text>
      <text class="sheet-text item-price" x="297" y="248">$24</text>

      <text class="sheet-text item-name" x="297" y="286">MINESTRONE SOUP</text>
      <text class="sheet-text item-detail" x="297" y="308">Served with Garlic Bread</text>
      <text class="sheet-text item-price" x="297" y="338">$8</text>
    </g>

    <g class="cocktail-special">
      <text class="sheet-text section-title" x="297" y="397">COCKTAIL SPECIAL</text>
      <text class="sheet-text item-name item-name--drink" x="297" y="435">PASSIONISTA</text>
      <text class="sheet-text item-detail" x="297" y="459">Vodka, Passionfruit Pulp, Mango Puree</text>
      <text class="sheet-text item-detail" x="297" y="478">Top up with Ginger &amp; Lemon Kombucha</text>
      <text class="sheet-text item-price" x="297" y="508">$17</text>
    </g>

    <g class="beer-special">
      <text class="sheet-text section-title" x="297" y="566">CRAFT BEER SPECIAL</text>
      <text class="sheet-text item-name item-name--drink" x="297" y="605">WANDERING GECKO</text>
      <text class="sheet-text item-detail" x="297" y="627">SUN PUNCH</text>
      <text class="sheet-text item-detail" x="297" y="646">Tropical Pale Ale</text>
      <text class="sheet-text item-detail" x="297" y="666">4.8% Alc.</text>
      <text class="sheet-text item-price" x="297" y="695">$10</text>
    </g>

    <rect class="vine-ornament" x="238" y="758" width="122" height="30" rx="15"
          role="img" aria-label="Small hand-drawn leafy vine ornament"/>
  </svg>
</main>
</body>
</html>
```